Business Card for Fashion House

We need a business card design for our personalize fashion service for our customers. the business card should reflect reliability, luxury and creativity.
The brand Gravetto is extracted from "Graceful Velvetto"; Gravetto provides fashion designs sprinkled with luxury and style tailored for our elite clients character profile.
Gravetto is created for those who embody class and elegance with a passion for style.
Target Market(s)
Affluent Customers
Industry/Entity Type
Fashion
Contact Information for Business Card
Samira Haddadin
Fashion Designer
Telephone: +971 4 555 0192
Mobile +971 50 555 0147
Emal info@gravetto-example.com
Website www.gravetto-example.com
Social Media Youtube g+ Facebook Instagram Pin /gravetto
Font styles to use
Other font styles liked:
- Audrey provided
Look and feel
Each slider illustrates characteristics of the customer's brand and the style your logo design should communicate.

```html
<!DOCTYPE html>
<html lang="en">
<head>
<meta charset="utf-8">
<title>Gravetto — Business Card</title>
<link href="https://fonts.googleapis.com/css2?family=Marcellus&family=Roboto:wght@400&display=swap" rel="stylesheet">
<style>
  :root {
    --backdrop: #3a3a3c;
    --card: #1c1c1e;
    --silver: #c9c9cc;
    --silver-dim: #8d8d92;
    --ink: #f2f2f2;
    --muted: #b9b9bd;
    --rule: #9a9a9e;
  }
  * { margin: 0; padding: 0; box-sizing: border-box; }
  html, body { width: 799px; height: 1200px; overflow: hidden; }
  body {
    background: var(--backdrop);
    display: flex;
    flex-direction: column;
  }
  .card-slot {
    height: 600px;
    display: flex;
    align-items: center;
    justify-content: center;
  }
  .card {
    width: 620px;
    height: 354px;
    background: var(--card);
    border-radius: 4px;
    box-shadow: 0 12px 30px rgba(0,0,0,0.45);
    position: relative;
  }

  /* Front */
  .card-front {
    display: flex;
    flex-direction: column;
    align-items: center;
    justify-content: center;
    gap: 26px;
  }
  .brand-dot {
    width: 64px;
    height: 64px;
    border-radius: 50%;
    border: 3px solid var(--silver);
  }
  .brand-name {
    font-family: "Marcellus", serif;
    font-size: 40px;
    letter-spacing: 0.42em;
    margin-right: -0.42em;
    color: var(--silver);
  }

  /* Back */
  .card-back {
    display: flex;
    align-items: center;
    padding: 0 44px;
  }
  .identity {
    width: 250px;
    text-align: right;
    padding-right: 28px;
  }
  .identity-name {
    font-family: "Marcellus", serif;
    font-size: 26px;
    color: var(--ink);
  }
  .identity-role {
    font-family: "Roboto", sans-serif;
    font-size: 13px;
    color: var(--muted);
    margin-top: 6px;
  }
  .identity-social {
    display: flex;
    align-items: center;
    justify-content: flex-end;
    gap: 8px;
    margin-top: 10px;
    font-family: "Roboto", sans-serif;
    font-size: 17px;
    color: var(--muted);
  }
  .social-dot {
    width: 12px;
    height: 12px;
    border-radius: 50%;
    background: var(--silver-dim);
  }
  .divider {
    width: 1px;
    height: 170px;
    background: var(--rule);
  }
  .contacts {
    list-style: none;
    padding-left: 30px;
    margin-top: 70px;
    font-family: "Roboto", sans-serif;
    font-size: 16px;
    color: var(--ink);
  }
  .contacts li {
    display: flex;
    align-items: center;
    gap: 10px;
    line-height: 24px;
  }
  .contacts svg {
    width: 15px;
    height: 15px;
    flex: none;
    fill: none;
    stroke: var(--ink);
    stroke-width: 1.6;
  }
</style>
</head>
<body>
  <section class="card-slot">
    <div class="card card-front">
      <div class="brand-dot"></div>
      <div class="brand-name">GRAVETTO</div>
    </div>
  </section>

  <section class="card-slot">
    <div class="card card-back">
      <div class="identity">
        <div class="identity-name">Samira Haddadin</div>
        <div class="identity-role">Fashion Designer</div>
        <div class="identity-social"><span class="social-dot"></span>/gravetto</div>
      </div>
      <div class="divider"></div>
      <ul class="contacts">
        <li>
          <svg viewBox="0 0 16 16"><path d="M4 2l2.5 3-1.5 1.5c.8 1.8 2.2 3.2 4 4L10.5 9 13.5 11.5 12 14C7 14 2 9 2 4z"/></svg>
          +971 4 555 0192
        </li>
        <li>
          <svg viewBox="0 0 16 16"><rect x="4.5" y="1.5" width="7" height="13" rx="1.2"/><line x1="7" y1="12" x2="9" y2="12"/></svg>
          +971 50 555 0147
        </li>
        <li>
          <svg viewBox="0 0 16 16"><rect x="1.5" y="3.5" width="13" height="9"/><path d="M1.5 3.5L8 9l6.5-5.5"/></svg>
          info@gravetto-example.com
        </li>
        <li>
          <svg viewBox="0 0 16 16"><circle cx="8" cy="8" r="6.5"/><ellipse cx="8" cy="8" rx="2.8" ry="6.5"/><line x1="1.5" y1="8" x2="14.5" y2="8"/></svg>
          www.gravetto-example.com
        </li>
      </ul>
    </div>
  </section>
</body>
</html>
```